Meridale Bed Company Needs Business Card

Looking for a very nice looking business card. Creative but not extravagant. We sell beds and pillows across the U.S. and need something professional but catchy. I have attached the logo.

Name : Devin Holt
Title : President
Phone : (800) 471-2960
Email: sleep@quilmora.com
Website: www.quilmora.com

Can be single-sided or double-sided
horizontal or vertical

Can use Blues/Greys

Target Market(s)

Mass Market

Industry/Entity Type

Retail

Contact Information for Business Card

Name : Devin Holt
Title : President
Phone : (800) 471-2960
Email: sleep@quilmora.com
Website: www.quilmora.com

Requirements
Must have
• Clean, Modern, Smooth
• Can use Blues/Greys
• On the other side without the information - have something simple like www.quilmora.com or our logo
Nice to have
• Surprise me
Should not have
• Nothing crazy, nothing cluttered

```html
<!DOCTYPE html>
<html lang="en">
<head>
<meta charset="utf-8">
<title>Quilmora Business Card</title>
<link rel="stylesheet" href="https://fonts.googleapis.com/css2?family=Quicksand:wght@300;400;500;700&display=swap">
<style>
  :root {
    --brand-blue: #32a5d8;
    --band-grey: #a7a8aa;
    --band-grey-light: #bfc0c2;
    --ink-grey: #4a4a4a;
    --card-white: #ffffff;
    --page-bg: #eeeff0;
  }
  * { box-sizing: border-box; margin: 0; padding: 0; }
  html, body {
    width: 1200px;
    height: 800px;
    overflow: hidden;
    background: var(--page-bg);
    font-family: "Quicksand", sans-serif;
  }
  .canvas {
    width: 1200px;
    height: 800px;
    display: flex;
    align-items: center;
    justify-content: center;
    gap: 50px;
  }
  .card {
    position: relative;
    width: 540px;
    height: 309px;
    overflow: hidden;
    box-shadow: 0 2px 6px rgba(0,0,0,0.08);
  }
  .card-shapes {
    position: absolute;
    inset: 0;
    width: 100%;
    height: 100%;
  }

  /* Back side */
  .card-back { background: var(--brand-blue); }
  .card-back .brand-name {
    position: absolute;
    inset: 0;
    display: flex;
    align-items: center;
    justify-content: center;
    color: var(--card-white);
    font-weight: 300;
    font-size: 68px;
    letter-spacing: 1px;
  }

  /* Front side */
  .card-front { background: var(--card-white); }
  .holder {
    position: absolute;
    top: 34px;
    right: 22px;
    display: flex;
    align-items: flex-start;
    gap: 8px;
  }
  .holder-text { text-align: center; }
  .holder-name {
    color: var(--brand-blue);
    font-weight: 700;
    font-size: 19px;
    line-height: 1.1;
  }
  .holder-title {
    color: var(--ink-grey);
    font-weight: 500;
    font-size: 13px;
    letter-spacing: 0.5px;
  }
  .holder-icon { width: 24px; height: 24px; margin-top: 1px; }
  .front-brand {
    position: absolute;
    left: 24px;
    top: 104px;
    color: var(--brand-blue);
    font-weight: 300;
    font-size: 58px;
    letter-spacing: 1px;
  }
  .address {
    position: absolute;
    left: 18px;
    top: 268px;
    width: 270px;
    color: var(--card-white);
    font-weight: 500;
    font-size: 12.5px;
    line-height: 1.2;
  }
  .address .indent { padding-left: 34px; display: block; }
  .contacts {
    position: absolute;
    right: 20px;
    top: 220px;
    list-style: none;
    color: var(--card-white);
    font-weight: 500;
    font-size: 13.5px;
    letter-spacing: 0.3px;
  }
  .contacts li {
    display: flex;
    align-items: center;
    justify-content: flex-end;
    gap: 7px;
    line-height: 20px;
  }
  .contacts svg { width: 13px; height: 13px; flex: none; }
</style>
</head>
<body>
<main class="canvas">

  <section class="card card-back" aria-label="Card back">
    <div class="brand-name">quilmora</div>
  </section>

  <section class="card card-front" aria-label="Card front">
    <svg class="card-shapes" viewBox="0 0 540 309" aria-hidden="true">
      <!-- top bands -->
      <polygon points="0,0 540,0 540,10 292,10 276,30 0,30" fill="var(--brand-blue)"/>
      <polygon points="296,14 540,14 540,22 289,22" fill="var(--band-grey-light)"/>
      <!-- bottom left grey bands -->
      <polygon points="0,236 318,236 312,246 0,246" fill="var(--band-grey-light)"/>
      <polygon points="0,250 310,250 286,309 0,309" fill="var(--band-grey)"/>
      <!-- bottom right blue block -->
      <polygon points="334,212 540,212 540,309 298,309" fill="var(--brand-blue)"/>
    </svg>

    <div class="holder">
      <div class="holder-text">
        <div class="holder-name">Devin Holt</div>
        <div class="holder-title">President</div>
      </div>
      <svg class="holder-icon" viewBox="0 0 24 24" aria-hidden="true">
        <rect width="24" height="24" rx="4" fill="var(--band-grey)"/>
        <circle cx="12" cy="8" r="3.6" fill="#fff"/>
        <path d="M5 20 Q5 13 12 13 Q19 13 19 20 Z" fill="#fff"/>
      </svg>
    </div>

    <div class="front-brand">quilmora</div>

    <p class="address">Address line 1 , Address Line 2,<span class="indent">Address Line 3</span></p>

    <ul class="contacts">
      <li>(800) 471-2960
        <svg viewBox="0 0 13 13" aria-hidden="true"><rect width="13" height="13" rx="2" fill="#fff"/><path d="M3.5 3 L5.3 3 L5.8 5 L4.9 5.8 Q5.8 7.6 7.3 8.2 L8.1 7.3 L10 7.8 L10 9.6 Q6 10 3.5 5.5 Z" fill="var(--brand-blue)"/></svg>
      </li>
      <li>sleep@quilmora.com
        <svg viewBox="0 0 13 13" aria-hidden="true"><rect width="13" height="13" rx="2" fill="#fff"/><rect x="2.5" y="3.8" width="8" height="5.6" fill="none" stroke="var(--brand-blue)" stroke-width="1"/><path d="M2.5 3.8 L6.5 7 L10.5 3.8" fill="none" stroke="var(--brand-blue)" stroke-width="1"/></svg>
      </li>
      <li>www.quilmora.com
        <svg viewBox="0 0 13 13" aria-hidden="true"><rect width="13" height="13" rx="2" fill="#fff"/><circle cx="6.5" cy="6.5" r="3.8" fill="none" stroke="var(--brand-blue)" stroke-width="1"/><ellipse cx="6.5" cy="6.5" rx="1.6" ry="3.8" fill="none" stroke="var(--brand-blue)" stroke-width="0.8"/><line x1="2.7" y1="6.5" x2="10.3" y2="6.5" stroke="var(--brand-blue)" stroke-width="0.8"/></svg>
      </li>
    </ul>
  </section>

</main>
</body>
</html>
```